OpenHarbor Yoga Website Design

Business Logo - attached
5 pages being:
Home
About
Classes
Blog
Contact

Would like Scrolling webpage and yoga symbols to be used.

Must have's being:
Easy to navigate, Text needs to be able to be edited/updated, Enquire Now Links, More Information Links, be a secure site, SEO,

Please refer to attached document for the information for the body of the website.

Target Market(s)

Educators, Community Service, Health and Wellbeing, Mental Health

Industry/Entity Type

Yoga

Coding

Coded - Design and coding required

Number of Pages Required

5+ page

Font styles to use
Other font styles liked:
• Bella Bold BC

Colors
0094D4
00A9DD
6FCCEA
C7EBF8
E9F6FB
6B429C
8869AF
B7A5CE
E3DAEB
F3F0F8

Requirements
Must have
• Easy to navigate, Text needs to be able to be edited/updated, Enquire Now Links, More Information Links, be a secure site, SEO,
Nice to have
• Scrolling webpage, yoga symbols

```html
<!DOCTYPE html>
<html lang="en">
<head>
<meta charset="utf-8">
<title>OpenHarbor Yoga – Website Design</title>
<link href="https://fonts.googleapis.com/css2?family=Arimo:wght@400;700&family=Kaushan+Script&family=Lora:wght@400;700&display=swap" rel="stylesheet">
<style>
:root{
  --board:#ad8be8;
  --purple:#5b22c4;
  --purple-mid:#6b429c;
  --violet:#8c3fb0;
  --teal:#1ea7b0;
  --band:#25b1d0;
  --sky:#0094d4;
  --footer:#4b4589;
  --grey:#f4f4f5;
  --text:#4a4a4a;
  --white:#fff;
  --grad:linear-gradient(90deg,#6a2fc4,#1fa9b0);
  --bar:linear-gradient(90deg,#2e2f8c 0%,#1a9aa6 50%,#6b3fb0 100%);
}
*{box-sizing:border-box;margin:0;padding:0}
html,body{width:748px;height:1200px;overflow:hidden;background:var(--board)}
.board{position:absolute;left:0;top:0;width:1512px;height:2426px;transform:scale(.4947);transform-origin:0 0;font-family:Arimo,Arial,sans-serif;color:var(--text)}
.page{position:absolute;top:90px;background:var(--white);overflow:hidden}
.page--full{left:146px;width:568px;height:2246px}
.page--short{left:808px;width:571px;height:2062px}
.abs{position:absolute}
.topbar{left:0;top:0;width:100%;height:28px;background:var(--bar);color:#fff;font-size:8px;display:flex;justify-content:flex-end;align-items:center;gap:9px;padding-right:60px}
.topbar .script{font-family:"Kaushan Script",cursive;font-size:9px}
.dot{width:7px;height:7px;border:1px solid #fff;border-radius:50%;display:inline-block}
.logo{width:62px;height:62px;border-radius:50%;background:#fff;border:1px solid #d9cdef;display:flex;align-items:center;justify-content:center;text-align:center;font-family:Arimo,Arial,sans-serif;font-size:9px;line-height:1.2;color:#8a62cc;z-index:3}
.nav{top:48px;font-family:Lora,serif;font-size:9px;color:#333;display:flex;gap:22px}
.nav .active{color:var(--purple);border-bottom:2px solid var(--purple);padding-bottom:6px}
.btn{display:flex;align-items:center;justify-content:center;border-radius:14px;background:var(--grad);color:#fff;font-family:Lora,serif;font-weight:700}
.btn--nav{font-family:"Kaushan Script",cursive;font-weight:400;font-size:9px}
.hero{left:0;top:77px;width:100%;height:320px;background:linear-gradient(180deg,#c9d3dd 0%,#e7d5c6 45%,#c8b3a7 62%,#7d8a9c 80%,#5d6b80 100%)}
.hero-curve{left:0;top:300px;width:100%;height:110px}
.hero-title{font-family:"Kaushan Script",cursive;color:var(--teal);font-size:27px;line-height:1.1;white-space:nowrap;width:250px;text-align:center}
.script-h{font-family:"Kaushan Script",cursive;color:var(--purple);text-align:center;width:100%;line-height:1.1}
.photo{background:linear-gradient(135deg,#dcd3c8,#8f8b8e)}
.copy{font-size:8.3px;line-height:1.27}
.copy p+p{margin-top:9px}
.band{left:0;width:100%;height:183px;background:var(--band);color:#fff;text-align:center}
.band .script-h{color:#fff;font-size:30px;position:absolute;top:42px}
.band .lead{position:absolute;top:90px;left:110px;right:110px;font-size:8.3px;line-height:1.27}
.band .strong{position:absolute;top:134px;width:100%;font-size:15px;font-weight:700}
.sub{font-family:"Kaushan Script",cursive;color:var(--violet);font-size:21px;line-height:1.1;white-space:nowrap}
.list{list-style:none;font-size:8.2px;line-height:1.25}
.list li{position:relative;padding-left:10px;margin-bottom:6px}
.list li::before{content:"";position:absolute;left:0;top:2px;width:5px;height:5px;border:1.3px solid var(--purple-mid);border-radius:50%}
.accent{background:var(--grad)}
.center-copy{text-align:center;font-size:9.2px;line-height:1.3;color:#555}
.field{font-size:8.5px;color:#444;border-bottom:1px solid #ccc;padding-bottom:9px}
.footer{left:0;width:100%;background:var(--footer);color:#fff;font-size:7.6px}
.rule{height:1px;background:rgba(255,255,255,.3)}
.circle-photo{border-radius:50%}
.ring{border-radius:50%;border:3px solid}
.foot-h{font-family:"Kaushan Script",cursive;color:#c9b7f1;font-size:16px;line-height:1.1}
.foot-list{font-size:7.6px;line-height:1.9}
</style>
</head>
<body>
<div class="board">

<!-- Full page layout -->
<section class="page page--full">
  <div class="abs topbar"><span>✉ info@openharboryoga.example</span><span class="script">Call Us: 0400 555 128</span><span class="dot"></span><span class="dot"></span></div>
  <div class="abs logo" style="left:56px;top:8px">OpenHarbor<br>Yoga</div>
  <nav class="abs nav" style="left:203px"><span class="active">Home</span><span>About</span><span>Classes</span><span>Blog</span><span>Contact</span></nav>
  <div class="abs btn btn--nav" style="left:446px;top:40px;width:62px;height:24px">Enquire Now</div>

  <div class="abs hero photo" role="img" aria-label="Woman meditating cross-legged with raised joined hands at sunset over the sea"></div>
  <svg class="abs hero-curve" viewBox="0 0 568 110" preserveAspectRatio="none">
    <defs><linearGradient id="swA" x1="0" x2="1"><stop offset="0" stop-color="#6a2fc4"/><stop offset="1" stop-color="#1fa9b0"/></linearGradient></defs>
    <path d="M0 52 Q260 85 568 40 L568 110 L0 110Z" fill="url(#swA)"/>
    <path d="M0 68 Q270 105 568 50 L568 110 L0 110Z" fill="#fff"/>
  </svg>
  <div class="abs hero-title" style="left:300px;top:203px">OpenHarbor Yoga</div>
  <div class="abs btn" style="left:383px;top:250px;width:84px;height:23px;font-size:10px">Enquire Now</div>

  <h2 class="abs script-h" style="top:428px;font-size:30px">Welcome to OpenHarbor Yoga...</h2>
  <div class="abs" style="left:43px;top:598px;width:96px;height:88px;border:1.5px solid #d8ccf0"></div>
  <div class="abs photo" style="left:60px;top:490px;width:199px;height:181px;background:linear-gradient(135deg,#e9e4df,#b9b3ad 55%,#6d7488)" role="img" aria-label="Close-up of a person meditating cross-legged on a mat"></div>
  <div class="abs copy" style="left:268px;top:490px;width:228px">
    <p>OpenHarbor Yoga believe that you are never too young to benefit from and fall in love with yoga. My aim is to EMPOWER kids and teens to thrive by teaching life skills in Yoga, Mindfulness and Breathing techniques to deal with daily challenges and big emotions.</p>
    <p>OpenHarbor Yoga gives kids an opportunity to enjoy and experience yoga for themselves and primarily focuses on programs for Schools, Pre Schools and Early Learning Centres, Private Classes, Sporting Clubs, Martial Arts Schools, Scout Groups and Occupational Therapy Centres just to name a few.All classes are age appropriate and encourage children's natural drive to learn, move, and be creative.</p>
  </div>
  <div class="abs btn" style="left:268px;top:646px;width:111px;height:23px;font-size:10px">More Information</div>

  <div class="abs band" style="top:725px">
    <h2 class="script-h">Benefits of Yoga...</h2>
    <p class="lead">The benefits of yoga can last a lifetime. It is my aim &amp; passion to introduce yoga to kids of all ages and backgrounds so that they can not only experience the benefits of yoga but fall in love with the practice.</p>
    <p class="strong">Yoga benefits include:</p>
  </div>

  <div class="abs" style="left:0;top:908px;width:100%;height:867px;background:var(--grey)"></div>
  <h3 class="abs sub" style="left:60px;top:958px">Healthy bodies</h3>
  <ul class="abs list" style="left:60px;top:994px;width:205px">
    <li>Develops strong, flexible and healthy bodies</li><li>Promotes spinal alignment and good posture</li><li>Builds energy and stamina</li><li>Improves internal physical function - organs, digestion, elimination, circulation, and blood flow.</li><li>Helps breathing and lung capacity</li><li>Teaches the enjoyment of movement</li><li>Works the 'whole' body</li>
  </ul>
  <div class="abs accent" style="left:430px;top:1056px;width:92px;height:84px"></div>
  <div class="abs photo" style="left:277px;top:968px;width:233px;height:156px;background:linear-gradient(135deg,#b9c9d6,#e7e0d8 50%,#6d6a6c)" role="img" aria-label="Young woman sitting in prayer pose in a bedroom"></div>

  <div class="abs accent" style="left:29px;top:1265px;width:92px;height:84px"></div>
  <div class="abs photo" style="left:43px;top:1180px;width:232px;height:156px;background:linear-gradient(180deg,#c59a2e,#e7c46a 45%,#7a8f3a 80%,#4c8d35)" role="img" aria-label="Woman meditating on grass in warm sunlight"></div>
  <h3 class="abs sub" style="left:310px;top:1193px">Healthy minds</h3>
  <ul class="abs list" style="left:310px;top:1228px;width:230px">
    <li>Cultivates confidence and self-esteem</li><li>Develops concentration and attention</li><li>Clears the mind for better clarity and decision making</li><li>Helps relax and sleep better</li><li>Calms the nervous system</li><li>Learns to cope with stressful situations</li><li>Balances emotions</li>
  </ul>

  <h3 class="abs sub" style="left:60px;top:1404px">Healthy spirits</h3>
  <ul class="abs list" style="left:60px;top:1439px;width:205px">
    <li>Fosters creativity, expression and imagination</li><li>Cultivates kindness to themselves and others</li><li>Cultivates respect for self and others</li><li>Builds balance and inner quiet</li><li>Builds inner strength and resilience</li><li>Teaches self-awareness</li><li>Focuses on positive self-talk</li>
  </ul>
  <div class="abs" style="left:424px;top:1500px;width:92px;height:84px;background:linear-gradient(90deg,#6a2fc4,#1fa9b0)"></div>
  <div class="abs photo" style="left:268px;top:1411px;width:233px;height:157px;background:linear-gradient(135deg,#f0ece8,#d8d2cc 50%,#a49c98)" role="img" aria-label="Smiling woman sitting cross-legged in a bright room"></div>

  <div class="abs center-copy" style="left:80px;top:1639px;width:408px">
    <p>OpenHarbor Yoga combines all the benefits of traditional yoga and a lot of fun! We play games and practice engaging flows which get our bodies moving, then we take a quiet moment to be still and calm as we focus on our breathing.</p>
    <p style="margin-top:10px">OpenHarbor Yoga Kids will learn that relaxation is just as important as moving their bodies, and the exercises which they learn in class can easily be repeated at any time in their busy day to feel calm and grounded.</p>
  </div>

  <h2 class="abs script-h" style="top:1796px;font-size:30px">Contact Us</h2>
  <div class="abs field" style="left:93px;top:1848px;width:184px">Name:</div>
  <div class="abs field" style="left:291px;top:1848px;width:184px">Phone:</div>
  <div class="abs field" style="left:93px;top:1882px;width:184px">Email:</div>
  <div class="abs field" style="left:291px;top:1882px;width:184px">Subject:</div>
  <div class="abs field" style="left:93px;top:1916px;width:373px;padding-bottom:26px">Message:</div>
  <div class="abs btn" style="left:244px;top:1970px;width:79px;height:24px;font-size:9px">Submit Now</div>

  <footer class="abs footer" style="top:2026px;height:220px">
    <div class="abs logo" style="left:253px;top:32px;background:transparent;border:1px solid #c9b7f1;color:#c9b7f1">OpenHarbor<br>Yoga</div>
    <div class="abs rule" style="left:60px;top:124px;width:447px"></div>
    <div class="abs" style="left:0;top:138px;width:100%;text-align:center">☎ Phone: 0400 555 128 &nbsp;&nbsp;&nbsp; ✉ Email: info@openharboryoga.example &nbsp;&nbsp;&nbsp; ● Location: Fernbrook, Victoria Australia 3999</div>
    <div class="abs rule" style="left:60px;top:162px;width:447px"></div>
    <div class="abs" style="left:0;top:179px;width:100%;text-align:center">Copyright 2023 OpenHarbor Yoga. All rights are reserved. &nbsp;ABN: &nbsp;00 111 222 333</div>
    <div class="abs" style="left:274px;top:200px;display:flex;gap:5px"><span class="dot"></span><span class="dot"></span></div>
  </footer>
</section>

<!-- Short page layout -->
<section class="page page--short">
  <div class="abs topbar"><span>✉ info@openharboryoga.example</span><span class="script">Call Us: 0400 555 128</span><span class="dot"></span><span class="dot"></span></div>
  <div class="abs logo" style="left:56px;top:8px">OpenHarbor<br>Yoga</div>
  <nav class="abs nav" style="left:205px"><span class="active">Home</span><span>About</span><span>Classes</span><span>Blog</span><span>Contact</span></nav>
  <div class="abs btn btn--nav" style="left:450px;top:40px;width:62px;height:24px">Enquire Now</div>

  <div class="abs hero photo" role="img" aria-label="Woman meditating cross-legged with raised joined hands at sunset over the sea"></div>
  <svg class="abs hero-curve" viewBox="0 0 571 110" preserveAspectRatio="none">
    <defs><linearGradient id="swB" x1="0" x2="1"><stop offset="0" stop-color="#6a2fc4"/><stop offset="1" stop-color="#1fa9b0"/></linearGradient></defs>
    <path d="M0 52 Q260 85 571 40 L571 110 L0 110Z" fill="url(#swB)"/>
    <path d="M0 70 Q270 107 571 52 L571 110 L0 110Z" fill="#fff"/>
  </svg>
  <div class="abs hero-title" style="left:303px;top:206px">OpenHarbor Yoga</div>
  <div class="abs btn" style="left:386px;top:253px;width:84px;height:23px;font-size:10px">Enquire Now</div>

  <h2 class="abs script-h" style="top:430px;font-size:30px">Welcome to OpenHarbor Yoga...</h2>
  <div class="abs" style="left:53px;top:550px;width:60px;height:140px;border:1.5px solid #d8ccf0;border-radius:14px"></div>
  <div class="abs photo" style="left:61px;top:487px;width:189px;height:192px;border-radius:16px;background:linear-gradient(135deg,#e9e4df,#b9b3ad 55%,#6d7488)" role="img" aria-label="Close-up of a person meditating cross-legged on a mat"></div>
  <div class="abs copy" style="left:270px;top:493px;width:230px">
    <p>OpenHarbor Yoga believe that you are never too young to benefit from and fall in love with yoga. My aim is to EMPOWER kids and teens to thrive by teaching life skills in Yoga, Mindfulness and Breathing techniques to deal with daily challenges and big emotions.</p>
    <p>OpenHarbor Yoga gives kids an opportunity to enjoy and experience yoga for themselves and primarily focuses on programs for Schools, Pre Schools and Early Learning Centres, Private Classes, Sporting Clubs, Martial Arts Schools, Scout Groups and Occupational Therapy Centres just to name a few.All classes are age appropriate and encourage children's natural drive to learn, move, and be creative.</p>
  </div>
  <div class="abs btn" style="left:270px;top:650px;width:112px;height:23px;font-size:10px">More Information</div>

  <div class="abs band" style="top:729px">
    <h2 class="script-h">Benefits of Yoga...</h2>
    <p class="lead">The benefits of yoga can last a lifetime. It is my aim &amp; passion to introduce yoga to kids of all ages and backgrounds so that they can not only experience the benefits of yoga but fall in love with the practice.</p>
    <p class="strong">Yoga benefits include:</p>
  </div>

  <svg class="abs" style="left:0;top:910px" width="571" height="800" viewBox="0 0 571 800">
    <defs>
      <linearGradient id="blobP" x1="0" x2="1"><stop offset="0" stop-color="#9a48b4"/><stop offset="1" stop-color="#7043a0"/></linearGradient>
      <linearGradient id="blobB" x1="0" x2="1"><stop offset="0" stop-color="#22a6d3"/><stop offset="1" stop-color="#5f49a4"/></linearGradient>
    </defs>
    <path d="M340 0 L571 0 L571 266 L320 266 Q300 200 340 150 Q395 80 340 0Z" fill="url(#blobP)"/>
    <rect x="0" y="266" width="571" height="268" fill="#f4f4f5"/>
    <path d="M0 266 L190 266 Q150 330 170 400 Q190 470 180 534 L0 534Z" fill="#e3eff2"/>
    <path d="M340 534 L571 534 L571 800 L320 800 Q300 740 340 690 Q395 620 340 534Z" fill="url(#blobB)"/>
  </svg>

  <h3 class="abs sub" style="left:62px;top:958px">Healthy bodies</h3>
  <ul class="abs list" style="left:62px;top:993px;width:210px">
    <li>Develops strong, flexible and healthy bodies</li><li>Promotes spinal alignment and good posture</li><li>Builds energy and stamina</li><li>Improves internal physical function - organs, digestion, elimination, circulation, and blood flow.</li><li>Helps breathing and lung capacity</li><li>Teaches the enjoyment of movement</li><li>Works the 'whole' body</li>
  </ul>
  <div class="abs ring" style="left:278px;top:940px;width:204px;height:204px;border-color:#c9a4e8"></div>
  <div class="abs ring" style="left:287px;top:949px;width:186px;height:186px;border-color:#fff"></div>
  <div class="abs photo circle-photo" style="left:297px;top:959px;width:166px;height:166px;background:linear-gradient(135deg,#b9c9d6,#e7e0d8 50%,#6d6a6c)" role="img" aria-label="Young woman sitting in prayer pose in a bedroom"></div>

  <div class="abs ring" style="left:68px;top:1207px;width:204px;height:204px;border-color:#a9d6da"></div>
  <div class="abs ring" style="left:77px;top:1216px;width:186px;height:186px;border-color:#6b2fc4"></div>
  <div class="abs photo circle-photo" style="left:87px;top:1226px;width:166px;height:166px;background:linear-gradient(180deg,#c59a2e,#e7c46a 45%,#7a8f3a 80%,#4c8d35)" role="img" aria-label="Woman meditating on grass in warm sunlight"></div>
  <h3 class="abs sub" style="left:312px;top:1236px">Healthy minds</h3>
  <ul class="abs list" style="left:312px;top:1270px;width:240px">
    <li>Cultivates confidence and self-esteem</li><li>Develops concentration and attention</li><li>Clears the mind for better clarity and decision making</li><li>Helps relax and sleep better</li><li>Calms the nervous system</li><li>Learns to cope with stressful situations</li><li>Balances emotions</li>
  </ul>

  <h3 class="abs sub" style="left:62px;top:1503px">Healthy spirits</h3>
  <ul class="abs list" style="left:62px;top:1538px;width:210px">
    <li>Fosters creativity, expression and imagination</li><li>Cultivates kindness to themselves and others</li><li>Cultivates respect for self and others</li><li>Builds balance and inner quiet</li><li>Builds inner strength and resilience</li><li>Teaches self-awareness</li><li>Focuses on positive self-talk</li>
  </ul>
  <div class="abs ring" style="left:278px;top:1478px;width:204px;height:204px;border-color:#9ed4f0"></div>
  <div class="abs ring" style="left:287px;top:1487px;width:186px;height:186px;border-color:#1e8fd6"></div>
  <div class="abs photo circle-photo" style="left:297px;top:1497px;width:166px;height:166px;background:linear-gradient(135deg,#f0ece8,#d8d2cc 50%,#a49c98)" role="img" aria-label="Smiling woman sitting cross-legged in a bright room"></div>

  <div class="abs center-copy" style="left:82px;top:1749px;width:408px">
    <p>OpenHarbor Yoga combines all the benefits of traditional yoga and a lot of fun! We play games and practice engaging flows which get our bodies moving, then we take a quiet moment to be still and calm as we focus on our breathing.</p>
    <p style="margin-top:10px">OpenHarbor Yoga Kids will learn that relaxation is just as important as moving their bodies, and the exercises which they learn in class can easily be repeated at any time in their busy day to feel calm and grounded.</p>
  </div>

  <footer class="abs footer" style="top:1870px;height:192px">
    <h4 class="abs foot-h" style="left:62px;top:26px">Contact Us</h4>
    <div class="abs foot-list" style="left:62px;top:52px">Contact: Clara Whitfield<br>Phone: 0400 555 128<br>Email: info@openharboryoga.example<br>Location: Fernbrook, Victoria Australia 3999</div>
    <div class="abs logo" style="left:255px;top:30px;background:transparent;border:1px solid #c9b7f1;color:#c9b7f1">OpenHarbor<br>Yoga</div>
    <h4 class="abs foot-h" style="left:353px;top:26px">Connect With Us</h4>
    <div class="abs foot-list" style="left:353px;top:52px"><span class="dot"></span> Social: OpenHarbor Yoga I Social<br><span class="dot"></span> Photos: openharboryoga4kids<br><span style="display:block;margin-top:6px">ABN: &nbsp;00 111 222 333</span></div>
    <div class="abs rule" style="left:62px;top:136px;width:448px"></div>
    <div class="abs" style="left:0;top:155px;width:100%;text-align:center;font-size:8px">Copyright 2023 OpenHarbor Yoga</div>
  </footer>
</section>

</div>
</body>
</html>
```